Website design for lighting products company

We want a design for our website. The website is for a company that sells lighting products. The structure is similar to the below website. We really like their design as well: www.palvenorlighting.com

Industry/Entity Type

Lighting

Number of Pages Required

5+ page

Colors

Designer to choose colors to be used in the design.

Requirements
Must have
• Simple design

```html
<!DOCTYPE html>
<html lang="en">
<head>
<meta charset="utf-8">
<title>Lumora Lighting</title>
<link href="https://fonts.googleapis.com/css2?family=Open+Sans:wght@400;600;700&display=swap" rel="stylesheet">
<style>
:root{
  --red:#9b1b20;
  --ink:#222222;
  --text:#444444;
  --grey-band:#efefef;
  --footer:#1f1f1f;
  --footer-text:#b5b5b5;
  --white:#ffffff;
}
*{margin:0;padding:0;box-sizing:border-box}
html,body{width:1200px;height:2408px;overflow:hidden}
body{position:relative;font-family:'Open Sans',Arial,sans-serif;background:var(--white);color:var(--text)}
.abs{position:absolute}
/* header */
.site-header{position:absolute;left:0;top:0;width:1200px;height:86px;background:var(--white)}
.brand{left:144px;top:18px;font-size:40px;font-weight:400;color:var(--ink);letter-spacing:-0.5px;line-height:48px}
.main-nav{left:471px;top:35px;display:flex;gap:29px;font-size:11.5px;color:#555;text-transform:uppercase}
.main-nav .active{color:var(--red)}
.icon-btn{top:25px;width:40px;height:40px;border-radius:50%;display:flex;align-items:center;justify-content:center}
.search-btn{left:951px;background:#e0e0e0}
.cart-btn{left:1014px;background:#222}
.cart-count{left:1005px;top:27px;width:19px;height:19px;border-radius:50%;background:var(--red);color:#fff;font-size:10px;text-align:center;line-height:19px}
/* hero */
.hero{left:0;top:86px;width:1200px;height:659px;background:linear-gradient(120deg,#cfcbd3 0%,#e2dbe0 35%,#c9a38a 55%,#d9d2d6 75%,#bfb9c0 100%);clip-path:polygon(0 0,100% 0,100% 531px,50% 659px,0 531px)}
.slide-arrow{top:326px;width:40px;height:48px;background:#2b2b2b;display:flex;align-items:center;justify-content:center}
.hero-title{left:147px;top:340px;font-size:33px;font-weight:700;color:#2a2a2a;line-height:40px;text-transform:uppercase}
.btn{display:flex;align-items:center;justify-content:center;background:var(--red);color:#fff;font-weight:600;text-transform:uppercase}
.shop-now{left:144px;top:426px;width:120px;height:40px;font-size:16px;font-weight:400}
/* sections */
.section-title{left:0;width:1200px;text-align:center;color:var(--red);font-size:33px;font-weight:700;text-transform:uppercase;line-height:40px}
.welcome-text{left:140px;top:866px;width:920px;text-align:center;font-size:13.6px;line-height:25.6px;color:#444}
.small-btn{width:112px;height:40px;font-size:13.5px}
.products-band{left:0;top:1100px;width:1200px;height:568px;background:var(--grey-band);clip-path:polygon(0 0,100% 0,100% 440px,50% 568px,0 440px)}
.product-card{top:1227px;width:218px;height:241px;background:#fff;box-shadow:0 0 4px rgba(0,0,0,.12);padding:5px}
.product-photo{width:208px;height:181px}
.product-name{text-align:center;font-size:17px;color:#555;margin-top:15px}
.brochure-card{top:1796px;width:297px;height:198px;background:#fff;border:4px solid #e9e9e9}
.brochure-photo{width:289px;height:102px}
.brochure-text{padding:16px 13px 0;font-size:10.5px;line-height:16px;color:#333}
.download-link{display:block;margin-top:6px;color:var(--red);text-decoration:underline;font-size:10.5px}
/* footer */
.site-footer{left:0;top:2136px;width:1200px;height:272px;background:var(--footer)}
.footer-heading{top:2172px;font-size:16px;color:#fff;font-weight:600;text-transform:uppercase}
.footer-links{top:2204px;font-size:11.5px;color:var(--footer-text);line-height:25.6px}
.contact-row{display:flex;align-items:center;gap:12px}
.social{top:2212px;width:40px;height:40px;border:1px solid #8a8a8a;border-radius:50%}
.footer-rule{left:144px;top:2330px;width:912px;height:1px;background:#555}
.copyright{left:0;top:2362px;width:1200px;text-align:center;font-size:11.5px;color:var(--footer-text)}
</style>
</head>
<body>
<header class="site-header">
  <div class="abs brand">Lumora Lighting</div>
  <nav class="abs main-nav">
    <span class="active">Home</span><span>About Us</span><span>Products</span><span>Solutions</span><span>Contact Us</span><span>Cart</span>
  </nav>
  <div class="abs icon-btn search-btn"><svg width="14" height="14" viewBox="0 0 14 14"><circle cx="6" cy="6" r="4.2" fill="none" stroke="#222" stroke-width="2"/><line x1="9" y1="9" x2="12.5" y2="12.5" stroke="#222" stroke-width="2.2"/></svg></div>
  <div class="abs icon-btn cart-btn"><svg width="14" height="13" viewBox="0 0 14 13"><path d="M0 1h3l2 7h7l2-5H4" fill="none" stroke="#fff" stroke-width="1.6"/><circle cx="6" cy="11" r="1.3" fill="#fff"/><circle cx="11" cy="11" r="1.3" fill="#fff"/></svg></div>
  <div class="abs cart-count">0</div>
</header>

<div class="abs hero" role="img" aria-label="Photograph of assorted pendant lamps hanging against a pale wall"></div>
<div class="abs slide-arrow" style="left:0"><svg width="18" height="20" viewBox="0 0 18 20"><path d="M13 2 5 10l8 8" fill="none" stroke="#fff" stroke-width="4"/></svg></div>
<div class="abs slide-arrow" style="left:1160px"><svg width="18" height="20" viewBox="0 0 18 20"><path d="M5 2l8 8-8 8" fill="none" stroke="#fff" stroke-width="4"/></svg></div>
<h1 class="abs hero-title">Etiam mattis<br>vehicula odio</h1>
<div class="abs btn shop-now">Shop Now</div>

<h2 class="abs section-title" style="top:816px">Welcome to Lumora Lighting</h2>
<p class="abs welcome-text">Nulla tristique posuere molestie. Aliquam erat volutpat. Etiam quis aliquet risus. Duis ornare erat eget magna dapibus, in accumsan quam pharetra. Nam tempus, quam in bibendum vulputate, sapien dolor viverra nisl, vitae euismod elit turpis et nulla. Aliquam erat volutpat. Pellentesque blandit lacus eget nunc faucibus, et tincidunt eros viverra. Phasellus consequat sagittis nisi suscipit feugiat. Cras eget leo sed nunc hendrerit ultricies eu at nisl. Praesent iaculis faucibus urna sit amet lacinia.</p>
<div class="abs btn small-btn" style="left:544px;top:981px">Read More</div>

<div class="abs products-band"></div>
<h2 class="abs section-title" style="top:1172px">Products</h2>
<div class="abs product-card" style="left:144px"><div class="product-photo" role="img" aria-label="Photo of a white wall-mounted indoor light" style="background:linear-gradient(135deg,#d6d6d6,#c4c4c4)"></div><div class="product-name">Indoor Lights</div></div>
<div class="abs product-card" style="left:375px"><div class="product-photo" role="img" aria-label="Photo of a bulb inside a black geometric outdoor lantern" style="background:radial-gradient(circle at 60% 40%,#8a6a48,#2e2b29 70%)"></div><div class="product-name">Out door Lights</div></div>
<div class="abs product-card" style="left:607px"><div class="product-photo" role="img" aria-label="Photo of a green illuminated emergency exit sign" style="background:radial-gradient(circle at 50% 45%,#3f8a4a,#1a241c 65%)"></div><div class="product-name">Emergency Lights</div></div>
<div class="abs product-card" style="left:838px"><div class="product-photo" role="img" aria-label="Photo of a ceiling light being adjusted with a remote control" style="background:linear-gradient(135deg,#e9d9c6,#b99a7c)"></div><div class="product-name">Lighting Controls</div></div>
<div class="abs btn small-btn" style="left:544px;top:1498px">View All</div>

<h2 class="abs section-title" style="top:1741px">Download Brochures</h2>
<div class="abs brochure-card" style="left:144px"><div class="brochure-photo" role="img" aria-label="Photo of glowing glass pendant bulbs" style="background:linear-gradient(90deg,#c89a72,#e8e2dc,#b98a62)"></div><div class="brochure-text">Maecenas tortor accumsan quam varius imperdiet vel eget elit. Aenean facilisis tincidunt lectus.<span class="download-link">DOWNLOAD NOW</span></div></div>
<div class="abs brochure-card" style="left:451px"><div class="brochure-photo" role="img" aria-label="Photo of black pendant lamps over a kitchen" style="background:linear-gradient(180deg,#4a4c4e,#8b8d8c)"></div><div class="brochure-text">Vivamus efficitur ex condimentum, malesuada eros eget, feugiat nibh. Sed tellus ex.<span class="download-link">DOWNLOAD NOW</span></div></div>
<div class="abs brochure-card" style="left:759px"><div class="brochure-photo" role="img" aria-label="Photo of warm hanging bulbs among greenery" style="background:linear-gradient(90deg,#4a2a1a,#c2613a,#5a3020)"></div><div class="brochure-text">Etiam mattis augue vehicula odio posuere, sit amet tempus lectus luctus. Nulla facilisi.<span class="download-link">DOWNLOAD NOW</span></div></div>
<div class="abs btn small-btn" style="left:544px;top:2016px">View All</div>

<footer class="abs site-footer"></footer>
<div class="abs footer-heading" style="left:144px">Links</div>
<div class="abs footer-links" style="left:144px">Home<br>About Us<br>Products<br>Solutions</div>
<div class="abs footer-links" style="left:232px">Contact Us<br>Cart<br>My Account<br>Wishlist</div>
<div class="abs footer-heading" style="left:503px">Contact Us</div>
<div class="abs footer-links" style="left:503px">
  <div class="contact-row"><svg width="12" height="12" viewBox="0 0 12 12"><path d="M2 1l2 0 1 3-1.5 1a7 7 0 0 0 3.5 3.5L8 7l3 1v2l-1 1C5 11 1 7 1 2z" fill="#9a9a9a"/></svg>555 014 2290</div>
  <div class="contact-row"><svg width="12" height="10" viewBox="0 0 12 10"><rect x="0" y="0" width="12" height="10" fill="#9a9a9a"/><path d="M0 0l6 5 6-5" fill="none" stroke="#1f1f1f" stroke-width="1.2"/></svg>info@lumoralighting.com</div>
</div>
<div class="abs footer-heading" style="left:846px">Follow Us On</div>
<div class="abs social" style="left:847px" aria-label="Social profile"></div>
<div class="abs social" style="left:903px" aria-label="Social profile"></div>
<div class="abs social" style="left:959px" aria-label="Social profile"></div>
<div class="abs social" style="left:1015px" aria-label="Social profile"></div>
<div class="abs footer-rule"></div>
<div class="abs copyright">Copyright © 2019 Lumora Lighting. All rights reserved.</div>
</body>
</html>
```